Packaging design for a reclosable bag for our product

We have a logo, and we need to put it on packaging for our product and while we want the look to be simple, we want it to follow good design principles and also contain spaces for other product descriptions.

There will be 5 sizes at launch so I'd like 5 variations, one for each size.

I've included a few mockups of the type of bag that I made but they are all just rough ideas that I had.

I want the brand to look scientific and methodical and even a bit quirky, as in "wow this is a serious product but also a bit unusual."

```html
<!DOCTYPE html>
<html lang="en">
<head>
<meta charset="utf-8">
<title>Orben 5m Extra Large – Pouch Front</title>
<link href="https://fonts.googleapis.com/css2?family=Roboto+Condensed:wght@300;400;700;900&display=swap" rel="stylesheet">
<style>
  :root {
    --backdrop: #9b9b9f;
    --pouch-top: #161616;
    --pouch-bottom: #242424;
    --pouch-edge: #0e0e0e;
    --seal-line: #090909;
    --size-figure-dark: #2c2b2c;
    --size-figure-light: #4a4949;
    --size-label: #8f8f91;
    --spec-text: #e8e8e8;
    --brand: #f2f2f2;
  }
  * { margin: 0; padding: 0; box-sizing: border-box; }
  html, body {
    width: 1023px;
    height: 1200px;
    overflow: hidden;
    background: var(--backdrop);
  }
  .canvas {
    position: relative;
    width: 1023px;
    height: 1200px;
    background: var(--backdrop);
    font-family: "Roboto Condensed", "Arial Narrow", sans-serif;
  }
  .pouch {
    position: absolute;
    left: 250px;
    top: 142px;
    width: 557px;
    height: 955px;
    background: linear-gradient(170deg, var(--pouch-top) 0%, var(--pouch-bottom) 100%);
    border: 1px solid var(--pouch-edge);
  }
  .pouch__notch {
    position: absolute;
    top: 96px;
    width: 10px;
    height: 10px;
    border-radius: 50%;
    background: var(--backdrop);
  }
  .pouch__notch--left { left: -5px; }
  .pouch__notch--right { right: -5px; }
  .pouch__zip {
    position: absolute;
    left: 42px;
    right: 32px;
    top: 108px;
    height: 8px;
    border-top: 2px solid var(--seal-line);
    border-bottom: 2px solid var(--seal-line);
  }
  .brand {
    position: absolute;
    left: 218px;
    top: 436px;
    color: var(--brand);
    font-weight: 700;
    font-size: 112px;
    line-height: 0.8;
    letter-spacing: -1px;
  }
  .size-figure {
    position: absolute;
    left: 100px;
    top: 652px;
    font-weight: 900;
    font-size: 184px;
    line-height: 0.8;
    letter-spacing: -6px;
    background: linear-gradient(90deg, var(--size-figure-dark), var(--size-figure-light));
    -webkit-background-clip: text;
    background-clip: text;
    color: transparent;
  }
  .size-details {
    position: absolute;
    left: 329px;
    top: 674px;
  }
  .size-details__label {
    color: var(--size-label);
    font-weight: 400;
    font-size: 38px;
    letter-spacing: 2px;
    line-height: 1;
    margin-bottom: 16px;
  }
  .size-details__spec {
    color: var(--spec-text);
    font-weight: 300;
    font-size: 19px;
    letter-spacing: -0.4px;
    line-height: 1.15;
  }
  .size-details__spec strong { font-weight: 700; }
</style>
</head>
<body>
<main class="canvas">
  <section class="pouch" aria-label="Reclosable pouch front panel">
    <span class="pouch__notch pouch__notch--left"></span>
    <span class="pouch__notch pouch__notch--right"></span>
    <div class="pouch__zip"></div>
    <h1 class="brand">Orben</h1>
    <div class="size-figure">5m</div>
    <div class="size-details">
      <p class="size-details__label">Extra Large</p>
      <p class="size-details__spec">Simulated <strong>D65 CRI90+</strong></p>
      <p class="size-details__spec"><strong>6500K</strong> White Bias Lighting</p>
    </div>
  </section>
</main>
</body>
</html>
```